I need an amazing business card!

I am the principle in my own software company that develops zorPad and mobile applications. I require a great business card design. I've attached my corporate logo (Thanks Tomas!).
I would like the design to integrate the logo, my name, email address and skype account:
name Brent Olafsen
email brentolafsen@tavrik.com
skype brentolafsen.net
I would like the back of the card to have a "write on me area" similar to the "write on me" card on this page, row 6:
http://us.prindlewick.com/design-templates/business-cards/#industry=Computing%20%26%20IT
As far as the rest - it's all you!
Updates
1) Please add an example telephone number as well.
Industry/Entity Type
Software
Look and feel
Each slider illustrates characteristics of the customer's brand and the style your logo design should communicate.

```html
<!DOCTYPE html>
<html lang="en">
<head>
<meta charset="utf-8">
<title>Brent Olafsen – Business Card</title>
<link rel="stylesheet" href="https://fonts.googleapis.com/css2?family=Arimo:wght@700&family=Jura:wght@500;600&display=swap">
<style>
  :root {
    --page-bg: #e9e6e1;
    --card-dark: #1d2216;
    --card-mid: #3a412f;
    --brand-green: #9cc441;
    --brand-green-light: #b5d25a;
    --divider: rgba(255, 255, 255, 0.22);
    --panel: rgba(255, 255, 255, 0.09);
    --icon-fill: #f2f2f2;
    --icon-glyph: #2a3020;
    --write-line: #ffffff;
  }
  * { margin: 0; padding: 0; box-sizing: border-box; }
  html, body {
    width: 1200px;
    height: 1000px;
    overflow: hidden;
    background: var(--page-bg);
  }
  .canvas {
    position: relative;
    width: 1200px;
    height: 1000px;
  }
  .card {
    position: absolute;
    left: 275px;
    width: 650px;
    height: 390px;
    background: radial-gradient(ellipse at 45% 45%, var(--card-mid) 0%, var(--card-dark) 75%);
    box-shadow: 0 6px 18px rgba(0, 0, 0, 0.25);
    overflow: hidden;
  }
  .card--front { top: 90px; }
  .card--back { top: 520px; }

  /* Front */
  .brand {
    position: absolute;
    left: 45px;
    top: 128px;
    width: 170px;
    display: flex;
    flex-direction: column;
    align-items: center;
  }
  .brand__square {
    width: 96px;
    height: 96px;
    border-radius: 18px;
    background: var(--brand-green);
  }
  .brand__name {
    margin-top: 22px;
    font-family: "Jura", sans-serif;
    font-weight: 600;
    font-size: 28px;
    letter-spacing: 12px;
    margin-right: -12px;
    color: var(--brand-green);
  }
  .divider {
    position: absolute;
    left: 257px;
    top: 92px;
    width: 2px;
    height: 212px;
    background: var(--divider);
  }
  .contact-panel {
    position: absolute;
    left: 295px;
    top: 88px;
    width: 330px;
    height: 218px;
    background: var(--panel);
  }
  .contact-name {
    position: absolute;
    left: 330px;
    top: 108px;
    font-family: "Arimo", sans-serif;
    font-weight: 700;
    font-size: 34px;
    line-height: 44px;
    color: var(--brand-green-light);
    white-space: nowrap;
  }
  .contact-list {
    position: absolute;
    left: 312px;
    top: 168px;
    list-style: none;
  }
  .contact-list li {
    display: flex;
    align-items: center;
    height: 33px;
    font-family: "Jura", sans-serif;
    font-weight: 500;
    font-size: 16px;
    letter-spacing: 1px;
    color: var(--brand-green-light);
    white-space: nowrap;
  }
  .contact-list svg {
    width: 22px;
    height: 22px;
    margin-right: 10px;
    flex: none;
  }

  /* Back */
  .write-prompt {
    position: absolute;
    left: 50px;
    top: 86px;
    font-family: "Jura", sans-serif;
    font-weight: 600;
    font-size: 20px;
    color: var(--brand-green);
  }
  .write-line {
    position: absolute;
    left: 45px;
    width: 560px;
    height: 42px;
    background: var(--write-line);
  }
  .write-line:nth-of-type(1) { top: 120px; }
  .write-line:nth-of-type(2) { top: 188px; }
  .write-line:nth-of-type(3) { top: 256px; }
  .write-line:nth-of-type(4) { top: 324px; }
</style>
</head>
<body>
<main class="canvas">

  <section class="card card--front" aria-label="Business card front">
    <div class="brand">
      <div class="brand__square"></div>
      <div class="brand__name">tavrik</div>
    </div>

    <div class="divider"></div>
    <div class="contact-panel"></div>

    <h1 class="contact-name">Brent Olafsen</h1>

    <ul class="contact-list">
      <li>
        <svg viewBox="0 0 22 22" aria-hidden="true">
          <circle cx="11" cy="11" r="11" fill="var(--icon-fill)"/>
          <rect x="5" y="7" width="12" height="8" fill="none" stroke="var(--icon-glyph)" stroke-width="1.4"/>
          <path d="M5 7 L11 12 L17 7" fill="none" stroke="var(--icon-glyph)" stroke-width="1.4"/>
        </svg>
        brentolafsen@tavrik.com
      </li>
      <li>
        <svg viewBox="0 0 22 22" aria-hidden="true">
          <circle cx="11" cy="11" r="11" fill="var(--icon-fill)"/>
        </svg>
        brentolafsen.net
      </li>
      <li>
        <svg viewBox="0 0 22 22" aria-hidden="true">
          <circle cx="11" cy="11" r="11" fill="var(--icon-fill)"/>
          <path d="M5 9 Q11 4 17 9 L15.5 10.5 L13.5 9.5 L13.5 8.3 Q11 7.5 8.5 8.3 L8.5 9.5 L6.5 10.5 Z" fill="var(--icon-glyph)"/>
          <rect x="7" y="11" width="8" height="5" rx="1" fill="var(--icon-glyph)"/>
        </svg>
        (555) 384-9061
      </li>
      <li>
        <svg viewBox="0 0 22 22" aria-hidden="true">
          <circle cx="11" cy="11" r="11" fill="var(--icon-fill)"/>
          <g fill="none" stroke="var(--icon-glyph)" stroke-width="1.2">
            <circle cx="11" cy="11" r="6"/>
            <ellipse cx="11" cy="11" rx="2.6" ry="6"/>
            <line x1="5" y1="11" x2="17" y2="11"/>
            <line x1="6" y1="8" x2="16" y2="8"/>
            <line x1="6" y1="14" x2="16" y2="14"/>
          </g>
        </svg>
        www.tavrik.com
      </li>
    </ul>
  </section>

  <section class="card card--back" aria-label="Business card back">
    <p class="write-prompt">You can write one me</p>
    <div class="write-line"></div>
    <div class="write-line"></div>
    <div class="write-line"></div>
    <div class="write-line"></div>
  </section>

</main>
</body>
</html>
```